Computer consultant business card

Bexil Software is a newly started computer consulting company. It's a small one-man company that provides mostly Vornix applications but also websites in collaboration with designers. I'm running this company on the side of full time university studies.

I want the final design to be clean and memorable. Be creative! :)

Some inspiration:
http://www.pixelmarta.com/design/48317
http://www.pixelmarta.com/design/2739164/business-card-design-by-frostlynk
http://www.pixelmarta.com/design/604281/business-card-design-by-koralind-vestrabanu

See attachment for my company logo.
Updates

I would like to thank everyone for submitting! I'll need a couple of days to review and ultimately select a design.

Target Market(s)

Non-technical entrepreneurs and small companies.

Industry/Entity Type

University

Requirements
Must have
• My company logo.
In any way, both colors from my logo.
First- and last name, e-mail and phone number.
Double-sided design.
Nice to have
• Something creative with the symbol in my logo

```html
<!DOCTYPE html>
<html lang="en">
<head>
<meta charset="utf-8">
<title>Bexil Software – Business Card</title>
<link rel="stylesheet" href="https://fonts.googleapis.com/css2?family=Quicksand:wght@500;700&family=Open+Sans:wght@400;700&display=swap">
<style>
  :root {
    --stage: #e8e2d6;
    --label: #1c1c1c;
    --black: #0b0b0c;
    --charcoal: #333234;
    --white: #ffffff;
    --brand-blue: #4a72ba;
    --teal: #1a8fae;
    --ink: #2f2e30;
    --muted: #4b4b4b;
  }
  * { box-sizing: border-box; margin: 0; padding: 0; }
  html, body {
    width: 1200px; height: 788px; overflow: hidden;
    background: var(--stage);
    font-family: "Open Sans", Arial, sans-serif;
  }
  .sheet { position: relative; width: 1200px; height: 788px; }

  .view-label {
    position: absolute; width: 525px; text-align: center;
    font-size: 20px; color: var(--label);
  }
  .card {
    position: absolute; width: 525px; height: 300px;
    border-radius: 22px; overflow: hidden;
    box-shadow: 0 3px 8px rgba(0,0,0,.35);
  }
  .card-front  { left: 55px;  top: 75px;  background: var(--black); }
  .card-back-1 { left: 622px; top: 75px;  background: var(--white); }
  .card-back-2 { left: 55px;  top: 445px; background: var(--black); }
  .card-back-3 { left: 622px; top: 445px; background: var(--charcoal); }

  .swoosh { position: absolute; inset: 0; }

  .wordmark {
    position: absolute; display: flex; align-items: center;
    font-family: "Quicksand", sans-serif; font-weight: 700;
    letter-spacing: 1px; line-height: 1;
  }
  .wordmark .mark-dot {
    border-radius: 50%; background: var(--brand-blue); flex: none;
  }
  .wordmark-small { left: 40px; top: 28px; font-size: 50px; color: var(--white); gap: 14px; }
  .wordmark-small .mark-dot { width: 52px; height: 52px; }
  .wordmark-large { left: 70px; top: 82px; font-size: 92px; gap: 30px; }
  .wordmark-large .mark-dot { width: 110px; height: 110px; }
  .card-back-1 .wordmark-large { color: var(--ink); }
  .card-back-2 .wordmark-large,
  .card-back-3 .wordmark-large { color: var(--white); }

  .holder { position: absolute; right: 21px; top: 152px; text-align: right; }
  .holder-name { font-size: 17px; font-weight: 700; color: var(--brand-blue); }
  .holder-role { font-size: 12px; color: var(--brand-blue); margin-top: 2px; }

  .contact {
    position: absolute; right: 24px; bottom: 17px;
    display: flex; gap: 14px; font-size: 13px; color: var(--muted);
  }
  .contact-item { display: flex; align-items: center; gap: 5px; }
  .contact-item svg { width: 10px; height: 10px; fill: var(--muted); }

  .web-address {
    position: absolute; left: 0; right: 0; bottom: 30px; text-align: center;
    font-size: 17px; letter-spacing: 3.6px;
  }
  .card-back-1 .web-address { color: var(--ink); }
  .card-back-2 .web-address,
  .card-back-3 .web-address { color: var(--white); }

  .texture {
    position: absolute; width: 260px; height: 150px;
  }
  .texture-top { left: 20px; top: 0;
    background: radial-gradient(ellipse at 50% 20%, rgba(120,118,122,.55), rgba(0,0,0,0) 70%); }
  .texture-bottom { right: 40px; bottom: 0;
    background: radial-gradient(ellipse at 50% 60%, rgba(140,136,142,.55), rgba(0,0,0,0) 70%); }
</style>
</head>
<body>
<main class="sheet">

  <p class="view-label" style="left:55px; top:34px;">Front</p>
  <section class="card card-front">
    <svg class="swoosh" viewBox="0 0 525 300" preserveAspectRatio="none" aria-hidden="true">
      <path d="M0 283 C150 140 330 28 520 0 L525 0 L525 300 L0 300 Z" fill="var(--white)"/>
      <path d="M0 297 C160 152 345 40 525 3 L525 300 L0 300 Z" fill="var(--teal)"/>
      <path d="M14 300 C175 170 360 58 525 12 L525 300 Z" fill="var(--white)"/>
    </svg>
    <div class="wordmark wordmark-small"><span class="mark-dot"></span>bexil</div>
    <div class="holder">
      <p class="holder-name">Your Name</p>
      <p class="holder-role">Designation</p>
    </div>
    <div class="contact">
      <span class="contact-item">
        <svg viewBox="0 0 10 10"><path d="M2 0.5 L4 2.5 L3 3.8 C3.6 5 5 6.4 6.2 7 L7.5 6 L9.5 8 L8 9.5 C4 9.5 0.5 6 0.5 2 Z"/></svg>
        +12 345 6789
      </span>
      <span class="contact-item">
        <svg viewBox="0 0 10 10"><path d="M0.5 2 H9.5 V8 H0.5 Z M0.5 2 L5 5.5 L9.5 2" stroke="var(--white)" stroke-width="0.8"/></svg>
        info@website.com
      </span>
    </div>
  </section>

  <p class="view-label" style="left:622px; top:34px;">Back - 1</p>
  <section class="card card-back-1">
    <div class="wordmark wordmark-large"><span class="mark-dot"></span>bexil</div>
    <p class="web-address">www.website.com</p>
  </section>

  <p class="view-label" style="left:55px; top:404px;">Back - 2</p>
  <section class="card card-back-2">
    <div class="texture texture-top" role="img" aria-label="Perforated metal dot texture, upper left"></div>
    <div class="texture texture-bottom" role="img" aria-label="Perforated metal dot texture, lower right"></div>
    <div class="wordmark wordmark-large"><span class="mark-dot"></span>bexil</div>
    <p class="web-address">www.website.com</p>
  </section>

  <p class="view-label" style="left:622px; top:404px;">Back - 3</p>
  <section class="card card-back-3">
    <div class="wordmark wordmark-large"><span class="mark-dot"></span>bexil</div>
    <p class="web-address">www.website.com</p>
  </section>

</main>
</body>
</html>
```